Personal Chef Needs a Good Web Design

Hi everyone!
My name is Leo, I work as a private chef for last 10 years, traveling all around the world and cooking in private megayacht and villas.
I'm about to settle down in my hometown in Europe for a while. And therefore I need a website that will show my story, pics and recipes, nutritional advices and of course offer a Personal and Private Chef services( working for 4-5 families and bringing delicious food to their house).
My clients are extremely rich folks, but usually are down to earth ones.
I believe, the web site should be focused on attention to:
-VIP person's wife( as she is usually responsible for food for family) and be simple.
-to famous people agents and be on high level.

There will be about 10 different menus and 6 different service offers

--UPDATE--
Logo Design:
+My thoughts are- printed structure of the vegetable or fruit on a white font. Like you slice the buffalo tomato, put it in red paint and print it on the edge of the page. See attached files named logo. Can be any nice structured thing, like tomato, lemon, red cabbage etc.
+Classic logos with chef's hat or knives are good too.
+Need to have the space for me to add the name( the fonts can be provided)

Target Market(s)

Private person. 80% Russian clients.

Industry/Entity Type

Cooking

Coding

Coded - Design and coding required

Number of Pages Required

3 page

Requirements
Must have
• Contact form/ Request back call/ Schedule a free consultation
Nice to have
• The client will need to choose straight ahead from the range of services I offer, like:
• -Private Chef( cooking only for the client)
• -Personal Chef( cooking for around 5 clients, bringing the ready to be heated food to their door)
• -Romantic dinner for two
• -Professional Sommelier service
• -Build your kitchen( offering design, equipment and that will fit your requirements)
• -Other( flowers, waiters, barista, equipment rental)
• So this column should go right after the introduction/aboutme part and will lead to separate pages with how-it-works thing for each.

```html
<!DOCTYPE html>
<html lang="en">
<head>
<meta charset="utf-8">
<title>Leo Chef — Private Chef in Megayacht and Villas</title>
<link rel="stylesheet" href="https://fonts.googleapis.com/css2?family=Montserrat:wght@400;500;600;700&family=Open+Sans:wght@400;600;700&display=swap">
<style>
:root{
  --orange:#d3843f;
  --ink:#1f1f1f;
  --text:#555;
  --muted:#888;
  --line:#d8d8d8;
  --panel:#f4f4f4;
  --white:#fff;
}
*{box-sizing:border-box;margin:0;padding:0}
html,body{width:1200px;height:3586px;overflow:hidden;background:var(--white)}
body{font-family:"Open Sans",Arial,sans-serif;color:var(--text);font-size:13px;position:relative}
.page{position:relative;width:1200px;height:3586px;overflow:hidden}
.abs{position:absolute}
h1,h2,h3,h4{font-family:"Montserrat",Arial,sans-serif;color:var(--ink)}
.btn{position:absolute;display:flex;align-items:center;justify-content:center;font-family:"Montserrat",Arial,sans-serif;font-weight:700;font-size:11px;letter-spacing:.5px;text-transform:uppercase}
.btn-solid{background:var(--orange);color:var(--white)}
.btn-outline{border:1px solid var(--white);color:var(--white)}
.ticks{list-style:none}
.ticks li{display:flex;align-items:center;gap:14px;height:36px;font-size:12.5px}
.ticks svg{flex:none}

/* hero */
.hero{left:0;top:0;width:1200px;height:560px;background:radial-gradient(ellipse at 55% 45%,#6d4030 0%,#3a2820 45%,#1b1714 100%)}
.hero-brand{left:98px;top:34px;color:var(--white);font-family:"Montserrat",sans-serif;font-weight:700;font-size:22px;letter-spacing:.5px}
.hero-menu{left:1066px;top:28px}
.hero-logo{left:0;width:1200px;top:215px;text-align:center;color:var(--white);font-family:"Montserrat",sans-serif;font-weight:500;font-size:62px;letter-spacing:4px}
.hero-rule{left:470px;top:328px;width:260px;height:2px;background:rgba(255,255,255,.8)}
.hero-sub{left:0;width:1200px;top:348px;text-align:center;color:var(--white);font-family:"Montserrat",sans-serif;font-weight:500;font-size:29px}
.hero-dots{left:551px;top:500px;display:flex;gap:6px}
.hero-dots span{width:12px;height:12px;border-radius:50%;border:1.5px solid var(--white)}
.hero-dots span.on{background:var(--orange);border-color:var(--orange)}

/* how it works */
.how-title{left:0;width:1200px;top:608px;text-align:center;font-size:32px;font-weight:700}
.how-text{left:172px;width:856px;top:668px;text-align:center;font-size:12.5px;line-height:29px}
.how-text p+p{margin-top:20px}
.divider{left:98px;width:1004px;height:1px;background:var(--line)}

/* about */
.about-photo{left:98px;top:963px;width:347px;height:407px;border:1px solid #ccc;padding:6px;background:var(--white)}
.about-photo div{width:100%;height:100%;background:linear-gradient(160deg,#8a6a4e,#3f352c 60%,#d9d4cc)}
.about-title{left:502px;top:958px;font-size:32px;font-weight:600}
.about-text{left:502px;width:600px;top:1020px;font-size:12.5px;line-height:30px}
.about-text p+p{margin-top:31px}

/* bands */
.nutri{left:0;top:1434px;width:600px;height:450px;background:var(--panel)}
.nutri-photo{left:600px;top:1434px;width:600px;height:450px;background:linear-gradient(135deg,#e9e5df 0%,#9d8f80 45%,#3c4a4a 100%)}
.band-title{font-size:30px;font-weight:600;line-height:40px}
.band-text{font-size:12.5px;line-height:22px}
.service-photo{left:0;top:1884px;width:600px;height:449px;background:linear-gradient(160deg,#4f6f8c 0%,#3a4e5e 35%,#6b6660 70%,#b98a6a 100%)}
.service{left:600px;top:1884px;width:600px;height:449px;background:var(--orange);color:var(--white)}
.service .band-title{color:var(--white)}

/* menu */
.menu-title{left:0;width:1200px;top:2380px;text-align:center;font-size:32px;font-weight:600}
.card{position:absolute;width:492px;height:196px;border:1px solid #bbb;display:flex;background:var(--white)}
.card-photo{width:190px;height:100%}
.card-body{flex:1;padding:12px 16px}
.card h3{font-size:18px;font-weight:600;margin-bottom:6px}
.card .ticks li{height:26px;font-size:11.5px;gap:10px}
.card .more{font-family:"Montserrat",sans-serif;font-weight:700;font-size:11px;margin-top:6px}
.card.warm .card-body{background:var(--orange);color:var(--white)}
.card.warm h3{color:var(--white)}
.card.plain .more{color:var(--orange)}
.explore{left:502px;top:2925px;width:196px;height:41px;border:1px solid #aaa;color:var(--orange)}
.orange-rule{left:0;top:3024px;width:1200px;height:4px;background:var(--orange)}

/* contact */
.contact-title{left:0;width:1200px;top:3066px;text-align:center;font-size:32px;font-weight:600}
.sub-head{font-size:14px;font-weight:600}
.label{font-size:11px;color:var(--text)}
.field{position:absolute;border:1px solid #999;background:var(--white)}
.info-row{position:absolute;left:808px;display:flex;align-items:center;gap:22px;font-size:12px}
.info-icon{width:40px;height:40px;border-radius:50%;border:1.5px solid var(--orange);display:flex;align-items:center;justify-content:center}
.hours{left:808px;top:3400px;width:294px;font-size:12px}
.hours div{display:flex;height:26px;align-items:center}
.hours span:first-child{width:143px}
.footer-rule{left:98px;top:3511px;width:1004px;height:1px;background:var(--line)}
.copyright{left:98px;top:3541px;font-size:11.5px}
.social{left:951px;top:3534px;display:flex;gap:16px}
.social span{width:26px;height:26px;border-radius:3px;background:#9a9a9a}
</style>
</head>
<body>
<div class="page">

  <!-- Hero -->
  <section class="abs hero" role="img" aria-label="Close-up of a plated salmon fillet with lemon and fresh herbs on a wooden board"></section>
  <div class="abs hero-brand">LEO CHEF</div>
  <svg class="abs hero-menu" width="34" height="34" viewBox="0 0 34 34" aria-hidden="true"><circle cx="17" cy="17" r="15" fill="none" stroke="#fff" stroke-width="2"/><rect x="11" y="12" width="12" height="2" fill="#fff"/><rect x="11" y="16" width="12" height="2" fill="#fff"/><rect x="11" y="20" width="12" height="2" fill="#fff"/></svg>
  <div class="abs hero-logo">LEO CHEF</div>
  <div class="abs hero-rule"></div>
  <div class="abs hero-sub">Private Chef in Megayacht and Villas</div>
  <div class="abs hero-dots"><span class="on"></span><span></span><span></span><span></span><span></span></div>

  <!-- How it works -->
  <h2 class="abs how-title">HOW IT WORKS</h2>
  <div class="abs how-text">
    <p>Our first consultation will be in your home. We will discuss any food preferences you may have, as well as any allergy or dietary needs. At this time we will also discuss what kind of meals you like, from meat and potatoes to all organic, vegan and vegetarian meals or international cuisine like Italian or Mexican. If you have concerns about your diet we can work with any restrictions you have.</p>
    <p>On your scheduled cook date we will prepare your meals in our commercial kitchen and drop them off to you at your convenience. Your meals will be chilled, packaged, labeled and stored in your refrigerator or freezer with easy instructions for heating. Meals can be packaged in single servings or family style. All meals will have special heating instructions which most only require you heating it up in the oven.</p>
  </div>
  <div class="abs divider" style="top:904px"></div>

  <!-- About -->
  <div class="abs about-photo"><div role="img" aria-label="Portrait of the chef in whites standing in a bakery kitchen"></div></div>
  <h2 class="abs about-title">LEO CHEF</h2>
  <div class="abs about-text">
    <p>At vero eos et accusamus et iusto odio dignissimos ducimus qui blanditiis praesentium voluptatum deleniti atque corrupti quos dolores et quas molestias excepturi.</p>
    <p>Sint occaecati cupiditate non provident, similique sunt in culpa qui officia deserunt mollitia animi, id est laborum et dolorum fuga. Et harum quidem rerum facilis est et expedita distinctio. Nam libero tempore, cum soluta nobis est eligendi optio cumque nihil impedit quo minus id quod maxime placeat facere possimus, omnis voluptas assumenda est, omnis dolor repellendus. Temporibus autem quibusdam et aut officiis debitis aut rerum necessitatibus saepe eveniet ut et voluptates. Et harum quidem rerum facilis est et expedita distinctio. Nam libero tempore, cum eligendi optio cumque nihil impe.</p>
  </div>
  <div class="btn btn-solid" style="left:502px;top:1334px;width:120px;height:31px">Read more &gt;&gt;</div>

  <!-- Nutritional advices -->
  <section class="abs nutri">
    <h2 class="abs band-title" style="left:98px;top:60px">NUTRITIONAL ADVICES</h2>
    <p class="abs band-text" style="left:98px;top:120px;width:470px">At vero eos et accusamus et iusto odio dignissimos ducimus qui blanditiis praesen tium voluptatum deleniti atque corrupti quoscaecati.</p>
    <ul class="abs ticks" style="left:98px;top:180px">
      <li><svg width="14" height="14" viewBox="0 0 14 14"><circle cx="7" cy="7" r="7" fill="var(--orange)"/><path d="M4 7.2l2 2 4-4.2" fill="none" stroke="#fff" stroke-width="1.6"/></svg>Nam libero tempore, cum soluta nobis est eligendi optio ostru</li>
      <li><svg width="14" height="14" viewBox="0 0 14 14"><circle cx="7" cy="7" r="7" fill="var(--orange)"/><path d="M4 7.2l2 2 4-4.2" fill="none" stroke="#fff" stroke-width="1.6"/></svg>Debitis aut rerum necessitatibus saepe eveniet ut et voluptat</li>
      <li><svg width="14" height="14" viewBox="0 0 14 14"><circle cx="7" cy="7" r="7" fill="var(--orange)"/><path d="M4 7.2l2 2 4-4.2" fill="none" stroke="#fff" stroke-width="1.6"/></svg>Ut aut reiciendis voluptatibus maiores alias consequatur volup</li>
      <li><svg width="14" height="14" viewBox="0 0 14 14"><circle cx="7" cy="7" r="7" fill="var(--orange)"/><path d="M4 7.2l2 2 4-4.2" fill="none" stroke="#fff" stroke-width="1.6"/></svg>Ut enim ad minima veniam, quis nostrum exercitationem ulum</li>
    </ul>
    <div class="btn btn-solid" style="left:98px;top:347px;width:120px;height:33px">Read more &gt;&gt;</div>
  </section>
  <div class="abs nutri-photo" role="img" aria-label="Chef's hands garnishing a plated dish with tweezers"></div>

  <!-- Personal & private chef services -->
  <div class="abs service-photo" role="img" aria-label="Dinner table set with wine glasses and seafood platters by the sea"></div>
  <section class="abs service">
    <h2 class="abs band-title" style="left:67px;top:54px">PERSONAL &amp; PRIVATE<br>CHEF SERVICES</h2>
    <p class="abs band-text" style="left:67px;top:140px;width:470px">At vero eos et accusamus et iusto odio dignissimos ducimus qui blanditiis praesen tium voluptatum deleniti atque corrupti quoscaecati.</p>
    <ul class="abs ticks" style="left:67px;top:197px">
      <li><svg width="14" height="14" viewBox="0 0 14 14"><circle cx="7" cy="7" r="7" fill="#fff"/><path d="M4 7.2l2 2 4-4.2" fill="none" stroke="var(--orange)" stroke-width="1.6"/></svg>Nam libero tempore, cum soluta nobis est eligendi optio ostru</li>
      <li><svg width="14" height="14" viewBox="0 0 14 14"><circle cx="7" cy="7" r="7" fill="#fff"/><path d="M4 7.2l2 2 4-4.2" fill="none" stroke="var(--orange)" stroke-width="1.6"/></svg>Debitis aut rerum necessitatibus saepe eveniet ut et voluptat</li>
      <li><svg width="14" height="14" viewBox="0 0 14 14"><circle cx="7" cy="7" r="7" fill="#fff"/><path d="M4 7.2l2 2 4-4.2" fill="none" stroke="var(--orange)" stroke-width="1.6"/></svg>Ut aut reiciendis voluptatibus maiores alias consequatur volup</li>
      <li><svg width="14" height="14" viewBox="0 0 14 14"><circle cx="7" cy="7" r="7" fill="#fff"/><path d="M4 7.2l2 2 4-4.2" fill="none" stroke="var(--orange)" stroke-width="1.6"/></svg>Ut enim ad minima veniam, quis nostrum exercitationem ulum</li>
    </ul>
    <div class="btn btn-outline" style="left:67px;top:363px;width:120px;height:33px">Read more &gt;&gt;</div>
  </section>

  <!-- Menu -->
  <h2 class="abs menu-title">PERSONAL CHEF MENU</h2>

  <article class="card warm" style="left:98px;top:2457px">
    <div class="card-photo" role="img" aria-label="Seafood tacos with red cabbage" style="background:linear-gradient(135deg,#c98a55,#7d5a8a 60%,#e7d9c6)"></div>
    <div class="card-body"><h3>SEAFOOD</h3>
      <ul class="ticks">
        <li><svg width="10" height="10" viewBox="0 0 10 10"><path d="M1 5.5l3 3 5-7" fill="none" stroke="#fff" stroke-width="2"/></svg>Thai Style Mahi with a Coconut Couscous</li>
        <li><svg width="10" height="10" viewBox="0 0 10 10"><path d="M1 5.5l3 3 5-7" fill="none" stroke="#fff" stroke-width="2"/></svg>Garlic and Herb Crusted Seabass</li>
        <li><svg width="10" height="10" viewBox="0 0 10 10"><path d="M1 5.5l3 3 5-7" fill="none" stroke="#fff" stroke-width="2"/></svg>Poached Halibut with Leeks &amp; Grape Tomatoes</li>
        <li><svg width="10" height="10" viewBox="0 0 10 10"><path d="M1 5.5l3 3 5-7" fill="none" stroke="#fff" stroke-width="2"/></svg>Miso Salmon with a Ginger Jasmine Rice</li>
      </ul><div class="more">VIEW MORE &gt;&gt;</div></div>
  </article>

  <article class="card plain" style="left:610px;top:2457px">
    <div class="card-photo" role="img" aria-label="Sliced medium-rare beef steak" style="background:linear-gradient(135deg,#3a2a22,#8c3b2e 55%,#d8cfc2)"></div>
    <div class="card-body"><h3>BEEF</h3>
      <ul class="ticks">
        <li><svg width="10" height="10" viewBox="0 0 10 10"><path d="M1 5.5l3 3 5-7" fill="none" stroke="var(--orange)" stroke-width="2"/></svg>Grilled Teriyaki Steak Tips</li>
        <li><svg width="10" height="10" viewBox="0 0 10 10"><path d="M1 5.5l3 3 5-7" fill="none" stroke="var(--orange)" stroke-width="2"/></svg>Slow Cooked Smokey Chipotle Tacos</li>
        <li><svg width="10" height="10" viewBox="0 0 10 10"><path d="M1 5.5l3 3 5-7" fill="none" stroke="var(--orange)" stroke-width="2"/></svg>Beef Tenderloin in a Mushroom Brandy Sauce</li>
        <li><svg width="10" height="10" viewBox="0 0 10 10"><path d="M1 5.5l3 3 5-7" fill="none" stroke="var(--orange)" stroke-width="2"/></svg>Penne Bolognese or Classic Meat Lasagna</li>
      </ul><div class="more">VIEW MORE &gt;&gt;</div></div>
  </article>

  <article class="card warm" style="left:98px;top:2677px">
    <div class="card-photo" role="img" aria-label="Chicken with mushrooms and herbs" style="background:linear-gradient(135deg,#6b5a3a,#b89a60 55%,#e5dccb)"></div>
    <div class="card-body"><h3>CHICKEN</h3>
      <ul class="ticks">
        <li><svg width="10" height="10" viewBox="0 0 10 10"><path d="M1 5.5l3 3 5-7" fill="none" stroke="#fff" stroke-width="2"/></svg>Chicken with Arugula with a Basil Pasta Salad</li>
        <li><svg width="10" height="10" viewBox="0 0 10 10"><path d="M1 5.5l3 3 5-7" fill="none" stroke="#fff" stroke-width="2"/></svg>Baked Chicken with Sweet Potato and Radish</li>
        <li><svg width="10" height="10" viewBox="0 0 10 10"><path d="M1 5.5l3 3 5-7" fill="none" stroke="#fff" stroke-width="2"/></svg>Marsala, Mushrooms, Pancetta, Marsala wine</li>
        <li><svg width="10" height="10" viewBox="0 0 10 10"><path d="M1 5.5l3 3 5-7" fill="none" stroke="#fff" stroke-width="2"/></svg>Curry Spiced Chicken Breast with a Yogurt</li>
      </ul><div class="more">VIEW MORE &gt;&gt;</div></div>
  </article>

  <article class="card plain" style="left:610px;top:2677px">
    <div class="card-photo" role="img" aria-label="Pan-fried pork chop with vegetables" style="background:linear-gradient(135deg,#5a2e1c,#a55a2e 55%,#d9c2a0)"></div>
    <div class="card-body"><h3>PORK</h3>
      <ul class="ticks">
        <li><svg width="10" height="10" viewBox="0 0 10 10"><path d="M1 5.5l3 3 5-7" fill="none" stroke="var(--orange)" stroke-width="2"/></svg>Oriental Sweet and Sour Pork</li>
        <li><svg width="10" height="10" viewBox="0 0 10 10"><path d="M1 5.5l3 3 5-7" fill="none" stroke="var(--orange)" stroke-width="2"/></svg>Maple Dijon Glazed Pork Medallions</li>
        <li><svg width="10" height="10" viewBox="0 0 10 10"><path d="M1 5.5l3 3 5-7" fill="none" stroke="var(--orange)" stroke-width="2"/></svg>Crispy Corn Flake Pan Fried Pork Chops</li>
        <li><svg width="10" height="10" viewBox="0 0 10 10"><path d="M1 5.5l3 3 5-7" fill="none" stroke="var(--orange)" stroke-width="2"/></svg>Creamy Pork Chops with Mushrooms, Haricot</li>
      </ul><div class="more">VIEW MORE &gt;&gt;</div></div>
  </article>

  <div class="btn explore">Explore more &gt;&gt;</div>
  <div class="abs orange-rule"></div>

  <!-- Contact -->
  <h2 class="abs contact-title">CONTACT US</h2>
  <h4 class="abs sub-head" style="left:98px;top:3146px">CONTACT FORM</h4>
  <span class="abs label" style="left:98px;top:3186px">NAME :</span>
  <span class="abs label" style="left:418px;top:3186px">PHONE NO :</span>
  <div class="field" style="left:98px;top:3217px;width:311px;height:34px"></div>
  <div class="field" style="left:418px;top:3217px;width:311px;height:34px"></div>
  <span class="abs label" style="left:98px;top:3258px">EMAIL :</span>
  <div class="field" style="left:98px;top:3281px;width:631px;height:34px"></div>
  <span class="abs label" style="left:98px;top:3322px">MESSAGE :</span>
  <div class="field" style="left:98px;top:3346px;width:631px;height:84px"></div>
  <div class="btn btn-solid" style="left:643px;top:3439px;width:86px;height:34px">Submit</div>

  <h4 class="abs sub-head" style="left:808px;top:3146px">CONTACT INFORMATION</h4>
  <div class="info-row" style="top:3187px">
    <span class="info-icon"><svg width="14" height="18" viewBox="0 0 14 18"><path d="M7 0C3 0 0 3 0 7c0 5 7 11 7 11s7-6 7-11c0-4-3-7-7-7z" fill="var(--orange)"/><circle cx="7" cy="7" r="2.5" fill="#fff"/></svg></span>
    <span style="line-height:20px">Street # 100 - 214<br>Harbor Town 88810</span>
  </div>
  <div class="info-row" style="top:3242px">
    <span class="info-icon"><svg width="18" height="18" viewBox="0 0 18 18"><circle cx="9" cy="9" r="9" fill="var(--orange)"/><rect x="4.5" y="6" width="9" height="6.5" fill="#fff"/><path d="M4.5 6l4.5 3.5L13.5 6" fill="none" stroke="var(--orange)" stroke-width="1"/></svg></span>
    <span>info@leochef.com</span>
  </div>
  <div class="info-row" style="top:3300px">
    <span class="info-icon"><svg width="16" height="16" viewBox="0 0 16 16"><path d="M3 1l3 3-1.5 2c1 2 3 4 5 5l2-1.5 3 3-2 2C7 14 2 9 1 3z" fill="var(--orange)"/></svg></span>
    <span>1 - 555 - 010 - 2020</span>
  </div>
  <h4 class="abs sub-head" style="left:808px;top:3372px">OPENING HOURS</h4>
  <div class="abs hours">
    <div><span>Monday - Wednesday</span><span>10:00 am - 10:00 pm</span></div>
    <div><span>Thursday &amp; Friday</span><span>10:00 am - 10:00 pm</span></div>
    <div><span>Saturday &amp; Sunday</span><span>9:00 am - 11:00 pm</span></div>
  </div>

  <div class="abs footer-rule"></div>
  <div class="abs copyright">Copyrights © 2016, Leo Chef . All Rights Reserved.</div>
  <div class="abs social" aria-label="Social links"><span></span><span></span><span></span><span></span></div>
</div>
</body>
</html>
```